Harbor & Crest Real estate

Design of business plans and presentations before and after of assets is required.
The design is of PowerPoint files and needs to be tailored to the US real estate market.
Graphs and relevant information is required about the area where the company property, Brookport Ohio is located.
To get acquainted with the logo, colors and guidelines of the existing company design, visit the website- www.hcqholdings.com

Seeking designer for long term collaborative work.

Font styles to use
Sans Serif

```html
<!DOCTYPE html>
<html lang="en">
<head>
<meta charset="utf-8">
<title>Harbor &amp; Crest – Maple Ridge Project Presentation</title>
<link href="https://fonts.googleapis.com/css2?family=Anton&family=Roboto:wght@400;500&family=Share+Tech+Mono&display=swap" rel="stylesheet">
<style>
:root{
  --yellow:#f0bf00;
  --black:#121212;
  --charcoal:#2a2a2a;
  --white:#ffffff;
  --ink:#1b1b1b;
  --canvas:#e4e4e4;
}
*{box-sizing:border-box;margin:0;padding:0}
html,body{width:1032px;height:1200px;overflow:hidden;background:var(--canvas)}
body{position:relative;font-family:"Roboto",sans-serif;color:var(--ink)}

.frame{position:absolute;transform-origin:top left}
.frame--cover{left:208px;top:162px;transform:scale(.78)}
.frame--small{transform:scale(.577)}
.pos-a{left:42px;top:628px}
.pos-b{left:535px;top:628px}
.pos-c{left:42px;top:911px}
.pos-d{left:535px;top:911px}

.slide{position:relative;width:780px;height:438px;overflow:hidden;background:var(--white);box-shadow:0 6px 16px rgba(0,0,0,.22)}
.dark-panel{position:absolute;left:0;right:0;background:radial-gradient(ellipse at 50% 40%,#3a3a3a 0%,#1c1c1c 55%,#0c0c0c 100%)}
.yellow-rule{position:absolute;left:0;right:0;height:9px;background:var(--yellow)}
.light-panel{position:absolute;left:0;right:0;top:0;background:linear-gradient(90deg,#fff 0%,#f1f1f1 100%)}

.dots{position:absolute;width:46px;height:30px;background-image:radial-gradient(circle,var(--yellow) 1.1px,transparent 1.4px);background-size:5px 5px}
.dots--white{background-image:radial-gradient(circle,#fff 1.1px,transparent 1.4px)}
.bars{position:absolute;width:20px;display:flex;flex-direction:column;gap:7px}
.bars span{display:block;height:3px;background:var(--yellow)}
.bars--white span{background:var(--white)}

.brand-name{font-family:"Share Tech Mono",monospace;color:var(--white);text-align:center;letter-spacing:.12em}
.brand-name .sub{display:block;font-size:.6em;letter-spacing:.08em;margin-top:4px}

.banner{position:absolute;background:var(--yellow);color:var(--black);font-family:"Anton",sans-serif;text-align:center;white-space:nowrap;clip-path:polygon(14px 0,calc(100% - 14px) 0,100% 50%,calc(100% - 14px) 100%,14px 100%,0 50%)}
.site{position:absolute;left:0;right:0;font-family:"Roboto",sans-serif;color:var(--white);text-align:center;letter-spacing:.28em}

/* cover */
.cover .light-panel{height:126px}
.cover .yellow-rule{top:126px}
.cover .dark-panel{top:135px;bottom:0}
.cover .brand-name{position:absolute;left:0;right:0;top:222px;font-size:34px}
.cover .banner{left:78px;width:624px;top:324px;height:48px;font-size:34px;line-height:48px}
.cover .site{top:390px;font-size:16px}

/* content pages */
.page-head{position:absolute;left:0;right:0;top:0;height:80px;background:linear-gradient(90deg,#fff,#f2f2f2);box-shadow:0 2px 4px rgba(0,0,0,.08)}
.page-title{position:absolute;left:48px;top:20px;font-family:"Anton",sans-serif;font-weight:400;font-size:28px;color:var(--black);letter-spacing:.01em;white-space:nowrap}
.mini-brand{position:absolute;right:30px;top:24px;font-family:"Share Tech Mono",monospace;font-size:9px;color:var(--charcoal);text-align:center;letter-spacing:.08em}
.mini-brand .sub{display:block;font-size:7px}
.page-foot{position:absolute;left:0;right:0;bottom:0;height:40px;background:linear-gradient(90deg,#111,#262626,#111);color:var(--white);font-size:14px;letter-spacing:.14em;text-align:center;line-height:40px}

.steps{position:absolute;left:42px;right:28px;top:106px;list-style:none}
.steps::before{content:"";position:absolute;left:17px;top:18px;bottom:20px;width:2px;background:var(--yellow)}
.step{position:relative;display:flex;align-items:flex-start;gap:12px;margin-bottom:22px;font-size:10.6px;line-height:1.5;text-align:justify}
.step-num{flex:none;width:34px;height:34px;border-radius:50%;background:var(--yellow);border:3px solid #fff;box-shadow:0 0 0 1px #d9a800;display:flex;align-items:center;justify-content:center;font-weight:500;font-size:14px;z-index:1}
.step p{padding-top:2px}

.body-text{position:absolute;font-size:10.6px;line-height:1.5;text-align:justify}
.body-text p+p{margin-top:14px}
.figure{position:absolute;border:2px solid var(--yellow);padding:4px;background:#fff}
.figure div{width:100%;height:100%}
.aerial{background:linear-gradient(160deg,#6d7d5c,#4f6145 50%,#8a8d85)}
.street-map{background:linear-gradient(135deg,#eef0ec,#dde4d8 60%,#e8e8e4)}

/* contact */
.contact .art{position:absolute;left:0;right:0;top:0;height:188px;background:linear-gradient(100deg,#fafafa 0%,#ececec 60%,#d9b89a 100%)}
.contact .yellow-rule{top:188px}
.contact .dark-panel{top:197px;bottom:0}
.contact .banner{left:296px;width:218px;top:169px;height:48px;font-size:30px;line-height:48px}
.contact-list{position:absolute;left:86px;top:260px;list-style:none;font-size:16px;color:var(--white)}
.contact-list li{margin-bottom:11px;white-space:nowrap}
.contact-list b{display:inline-block;width:80px;color:var(--yellow);font-weight:500}
.contact .brand-name{position:absolute;left:502px;width:240px;top:352px;font-size:15px}
</style>
</head>
<body>

<div class="frame frame--cover">
  <section class="slide cover">
    <div class="light-panel"></div>
    <div class="yellow-rule"></div>
    <div class="dark-panel"></div>
    <div class="dots" style="left:14px;top:8px" aria-hidden="true"></div>
    <div class="bars" style="right:0;top:50px"><span></span><span></span><span></span><span></span><span></span></div>
    <div class="bars bars--white" style="left:0;top:250px"><span></span><span></span><span></span><span></span><span></span><span></span></div>
    <div class="dots dots--white" style="right:6px;bottom:10px" aria-hidden="true"></div>
    <div class="brand-name">Harbor &amp; Crest<span class="sub">Group</span></div>
    <div class="banner">MAPLE RIDGE PROJECT - PLANS VS. EXECUTION</div>
    <div class="site">www.hcqholdings.com</div>
  </section>
</div>

<div class="frame frame--small pos-a">
  <section class="slide cover">
    <div class="light-panel"></div>
    <div class="yellow-rule"></div>
    <div class="dark-panel"></div>
    <div class="dots" style="left:14px;top:8px" aria-hidden="true"></div>
    <div class="bars" style="right:0;top:50px"><span></span><span></span><span></span><span></span><span></span></div>
    <div class="bars bars--white" style="left:0;top:250px"><span></span><span></span><span></span><span></span><span></span><span></span></div>
    <div class="dots dots--white" style="right:6px;bottom:10px" aria-hidden="true"></div>
    <div class="brand-name">Harbor &amp; Crest<span class="sub">Group</span></div>
    <div class="banner">MAPLE RIDGE PROJECT - PLANS VS. EXECUTION</div>
    <div class="site">www.hcqholdings.com</div>
  </section>
</div>

<div class="frame frame--small pos-b">
  <section class="slide">
    <header class="page-head">
      <div class="dots" style="left:8px;top:24px;width:34px" aria-hidden="true"></div>
      <h2 class="page-title">MAPLE RIDGE PROJECT - BACKGROUND</h2>
      <div class="mini-brand">Harbor &amp; Crest<span class="sub">Group</span></div>
      <div class="bars" style="right:0;top:20px;width:16px;gap:6px"><span></span><span></span><span></span><span></span></div>
    </header>
    <ol class="steps">
      <li class="step"><span class="step-num">1</span><p>Harbor &amp; Crest is an investment and real estate management company for U.S. assets specializing in providing significant and comprehensive benefits to its investors across the entire value chain of their investment from location, betterment and renovation, ongoing management and sales management.</p></li>
      <li class="step"><span class="step-num">2</span><p>The core of our real estate investment conduct lies first and foremost in locating transactions at the right price, with the central ambition being to locate assets at prices significantly lower than the market price.</p></li>
      <li class="step"><span class="step-num">3</span><p>Over the years, we have developed a unique method for locating Value Add assets in the activity areas at prices below market prices.</p></li>
      <li class="step"><span class="step-num">4</span><p>Today, the company manages over 500 properties and units in the United States, properties it has fully developed (locating-purchasing-renovating and building-operating and managing).</p></li>
      <li class="step"><span class="step-num">5</span><p>The company's team is made up entirely of company employees - from construction workers to management - enabling us to manage the transaction alongside a plan vs. execution model and to save on cost improvement and maximizing the overall return.</p></li>
    </ol>
    <footer class="page-foot">www.hcqholdings.com | Page-2</footer>
    <div class="bars" style="left:0;bottom:2px;width:16px;gap:6px"><span></span><span></span><span></span></div>
    <div class="dots dots--white" style="right:8px;bottom:4px;width:40px" aria-hidden="true"></div>
  </section>
</div>

<div class="frame frame--small pos-c">
  <section class="slide">
    <header class="page-head">
      <div class="dots" style="left:8px;top:24px;width:34px" aria-hidden="true"></div>
      <h2 class="page-title">MAPLE RIDGE PROJECT - LOCATING THE TRANSACTION</h2>
      <div class="mini-brand">Harbor &amp; Crest<span class="sub">Group</span></div>
      <div class="bars" style="right:0;top:20px;width:16px;gap:6px"><span></span><span></span><span></span><span></span></div>
    </header>
    <div class="body-text" style="left:42px;top:102px;width:476px">
      <p>Our locating system focuses on yielding assets with potential for improvement that are either partially occupied or upgradeable when the objective is to purchase assets below market price.</p>
      <p>The properties are located in developing areas and neighborhoods, close to top schools, universities, employment centers and major transport hubs.</p>
      <p>Within the locating system, we have developed unique methods for locating assets that do not exist or are not offered on the market for sale, and thus the brokerage price gaps can be saved.</p>
    </div>
    <div class="figure" style="left:539px;top:97px;width:198px;height:127px"><div class="aerial" role="img" aria-label="Aerial photograph of the Fairview neighborhood"></div></div>
    <div class="figure" style="left:42px;top:246px;width:198px;height:128px"><div class="street-map" role="img" aria-label="Street map marking the property location on Linden Avenue"></div></div>
    <div class="body-text" style="left:260px;top:241px;width:476px">
      <p>The Maple Ridge 1450 Project was located through locator Daniel Averill, who focused on the Fairview neighborhood, a central neighborhood among the three western neighborhoods in Brookport.</p>
      <p>After Daniel surveyed the area, he decided to focus his efforts on the central axis, Linden Avenue, which runs through the three western neighborhoods mentioned above.</p>
      <p>The property located is a multi-family with 18 housing units, with partial occupancy and considerable betterment potential.</p>
    </div>
    <footer class="page-foot">www.hcqholdings.com | Page-3</footer>
    <div class="bars" style="left:0;bottom:2px;width:16px;gap:6px"><span></span><span></span><span></span></div>
    <div class="dots dots--white" style="right:8px;bottom:4px;width:40px" aria-hidden="true"></div>
  </section>
</div>

<div class="frame frame--small pos-d">
  <section class="slide contact">
    <div class="art" role="img" aria-label="Hand with a marker drawing a flurry of sketched envelopes"></div>
    <div class="dots" style="left:14px;top:8px;width:38px" aria-hidden="true"></div>
    <div class="bars" style="right:0;top:40px;width:16px;gap:6px"><span></span><span></span><span></span><span></span></div>
    <div class="yellow-rule"></div>
    <div class="dark-panel"></div>
    <div class="banner">CONTACT US</div>
    <div class="bars bars--white" style="left:0;top:212px;width:18px;gap:6px"><span></span><span></span><span></span><span></span><span></span></div>
    <ul class="contact-list">
      <li><b>Address :</b> 14 Marina Way, Portside, Ohio</li>
      <li><b>Phone :</b> +1 555 010 2244</li>
      <li><b>Email :</b> office@hcqholdings.com</li>
      <li><b>Website :</b> www.hcqholdings.com</li>
    </ul>
    <div class="brand-name">Harbor &amp; Crest<span class="sub">Group</span></div>
    <div class="dots dots--white" style="left:110px;bottom:6px;width:34px;height:24px" aria-hidden="true"></div>
    <div class="dots" style="right:8px;bottom:6px;width:34px;height:28px" aria-hidden="true"></div>
  </section>
</div>

</body>
</html>
```